Prime Global Casting Agency Needs creative business card design

We manage actors careers and book them liaising and promoting their profiles internationally through Casting Directors, Producers, Directors, Publicists etc. We need clearly visable contact details but with a design that reflects our status and creativity of TV, Feature Film industry. Our logo is attached and needs to relate and our website is www.brisklanestagefolk.com
No flame designs please but please incorporate logo colours.

Target Market(s)

Clients

Industry/Entity Type

Film Production

Contact Information for Business Card

Director Danielle Prowse
Suite F, Building 4, Wrenlow Studios Australia, Kelby Vale, Sydney, NSW 2048

Font styles to use
Sans Serif

Colors
ec1f27

Requirements
Nice to have
• Colours should relate to logo attached and type can relate again to type in the logo design.
Should not have
• No Flames designs and best to be not too obvious with the film designs eiither. Needs to be more creative and modern

```html
<!DOCTYPE html>
<html lang="en">
<head>
<meta charset="utf-8">
<title>Prime Global Casting Agency – Business Card</title>
<link rel="stylesheet" href="https://fonts.googleapis.com/css2?family=Exo+2:wght@400;500;600;700&display=swap">
<style>
  :root {
    --brand-red: #ec1f27;
    --deep-red: #b3141b;
    --ink: #1e1e1e;
    --grey-text: #3a3a3a;
    --card-white: #ffffff;
    --card-grey: #ececec;
    --backdrop: #e4e1dc;
    --photo-light: #e9e4e0;
    --photo-warm: #c9a77a;
    --photo-blue: #4a3fb0;
  }
  * { box-sizing: border-box; margin: 0; padding: 0; }
  html, body {
    width: 1200px; height: 885px; overflow: hidden;
    background: var(--backdrop);
    font-family: "Exo 2", sans-serif;
  }
  .sheet {
    width: 1200px; height: 885px;
    display: flex; align-items: center; justify-content: center; gap: 50px;
  }
  .card {
    position: relative;
    width: 540px; height: 330px;
    background: linear-gradient(135deg, var(--card-white) 40%, var(--card-grey));
    box-shadow: 0 6px 18px rgba(0,0,0,.22);
    overflow: hidden;
  }
  /* Front */
  .card-front .portrait-area { position: absolute; inset: 0; }
  .card-front .details {
    position: absolute; left: 300px; top: 34px; right: 20px;
  }
  .brand-name {
    color: var(--brand-red);
    font-weight: 700;
    line-height: 1.05;
    text-transform: uppercase;
  }
  .card-front .brand-name { font-size: 23px; letter-spacing: .5px; }
  .person-name {
    margin-top: 30px;
    color: var(--brand-red);
    font-size: 21px; font-weight: 500;
  }
  .person-role { color: var(--ink); font-size: 17px; margin-top: 2px; }
  .contact-list { list-style: none; margin-top: 26px; }
  .contact-list li {
    color: var(--grey-text); font-size: 13.5px; line-height: 1.7;
    white-space: nowrap;
  }
  /* Back */
  .card-back .brand-block {
    position: absolute; left: 0; right: 0; top: 72px;
    display: flex; align-items: center; justify-content: center; gap: 12px;
  }
  .card-back .brand-mark {
    width: 18px; height: 18px; background: var(--brand-red); flex: none;
  }
  .card-back .brand-name { font-size: 34px; text-align: left; }
  .address-band {
    position: absolute; left: 0; right: 0; bottom: 0; height: 58px;
    background: linear-gradient(90deg, var(--deep-red), var(--brand-red));
    display: flex; align-items: center; justify-content: center;
  }
  .address-band address {
    font-style: normal; color: #fff; font-size: 15px; letter-spacing: .4px;
  }
</style>
</head>
<body>
<main class="sheet">
  <section class="card card-front">
    <svg class="portrait-area" width="540" height="330" viewBox="0 0 540 330">
      <defs>
        <linearGradient id="portraitFill" x1="0" y1="0" x2="1" y2="1">
          <stop offset="0" stop-color="var(--photo-light)"/>
          <stop offset=".55" stop-color="var(--photo-warm)"/>
          <stop offset="1" stop-color="var(--photo-blue)"/>
        </linearGradient>
      </defs>
      <path role="img" aria-label="Portrait photograph of the director"
            d="M0 0 H230 C300 90 250 230 280 330 H0 Z" fill="url(#portraitFill)"/>
      <path d="M230 0 C300 90 250 230 280 330" fill="none" stroke="var(--brand-red)" stroke-width="9"/>
      <path d="M244 0 C312 90 264 230 294 330" fill="none" stroke="var(--deep-red)" stroke-width="2"/>
    </svg>
    <div class="details">
      <p class="brand-name">Prime Global Casting Agency</p>
      <h1 class="person-name">Danielle Prowse</h1>
      <p class="person-role">Director</p>
      <ul class="contact-list">
        <li>+61 (0) 400 555 019</li>
        <li>danielle@brisklanestagefolk.com</li>
        <li>www.brisklanestagefolk.com</li>
      </ul>
    </div>
  </section>

  <section class="card card-back">
    <div class="brand-block">
      <span class="brand-mark"></span>
      <p class="brand-name">Prime Global<br>Casting Agency</p>
    </div>
    <div class="address-band">
      <address>Wrenlow Studios Australia, Kelby Vale, Sydney, NSW 2048</address>
    </div>
  </section>
</main>
</body>
</html>
```